Kinesiology undergraduate program needs an infographic

We would like an infographic to creatively and succinctly inform students, faculty, staff, and others about our undergraduate values and competencies (perhaps also integrating our mission and vision). We would like to see a design that incorporates the definition of Kinesiology (the study of human movement) and the colors of our Westbrook State University at Harlan.

```html
<!DOCTYPE html>
<html lang="en">
<head>
<meta charset="utf-8">
<title>Kinesiology Undergraduate Program — Westbrook State University at Harlan</title>
<link rel="stylesheet" href="https://fonts.googleapis.com/css2?family=Arimo:wght@400&family=Inter:wght@400&display=swap">
<style>
  :root {
    --navy: #15284b;
    --orange: #e64a2a;
    --green: #58842e;
    --gray-text: #7a7a7a;
    --bg-light: #ffffff;
    --bg-base: #e1e6eb;
  }
  * { margin: 0; padding: 0; box-sizing: border-box; }
  html, body { width: 985px; height: 1200px; overflow: hidden; }
  body {
    position: relative;
    font-family: "Arimo", Arial, sans-serif;
    color: var(--navy);
    background:
      radial-gradient(ellipse 560px 420px at 490px 230px, var(--bg-light) 0%, rgba(255,255,255,0.85) 40%, rgba(225,230,235,0) 100%),
      var(--bg-base);
  }
  .centered { position: absolute; transform: translateX(-50%); text-align: center; white-space: nowrap; }

  .program-title {
    left: 492px; top: 94px;
    font-size: 29px; line-height: 48px; font-weight: 400; letter-spacing: 0.2px;
  }

  .badge { position: absolute; top: 275px; width: 173px; height: 44px; }
  .badge-fill {
    position: absolute; left: 0; top: 3px; width: 169px; height: 41px;
  }
  .badge-frame {
    position: absolute; left: 3px; top: 0; width: 170px; height: 42px;
    border: 1.5px solid var(--navy);
  }
  .badge-label {
    position: absolute; left: 0; top: 3px; width: 172px; height: 41px;
    color: #fff; font-size: 28px; line-height: 41px; text-align: center;
  }
  .badge--mission { left: 108px; }
  .badge--mission .badge-fill { background: var(--orange); }
  .badge--vision { left: 393px; }
  .badge--vision .badge-fill { background: var(--navy); }
  .badge--values { left: 692px; }
  .badge--values .badge-fill { background: var(--green); }

  .statement {
    top: 352px; font-size: 11.6px; line-height: 15px; color: var(--gray-text);
  }
  .statement--mission { left: 196px; }
  .statement--vision { left: 481px; }
  .statement--values { left: 779px; }

  .competency-heading {
    left: 492px; top: 515px; font-size: 37px; line-height: 48px;
  }

  .domain {
    position: absolute; height: 42px; border: 1.5px solid var(--navy);
    font-size: 20px; line-height: 39px; text-align: center; white-space: nowrap;
  }
  .domain--science { left: 91px; top: 642px; width: 348px; }
  .domain--thinking { left: 567px; top: 642px; width: 305px; }
  .domain--relationships { left: 59px; top: 883px; width: 412px; }
  .domain--intrapersonal { left: 567px; top: 883px; width: 305px; }

  .skills {
    list-style: none; font-family: "Inter", Arial, sans-serif;
    font-size: 16px; line-height: 30px;
  }
  .skills--science { left: 265px; top: 713px; }
  .skills--thinking { left: 720px; top: 713px; }
  .skills--relationships { left: 265px; top: 954px; }
  .skills--intrapersonal { left: 718px; top: 954px; }
</style>
</head>
<body>
  <h1 class="program-title centered">KINESIOLOGY UNDERGRADUATE<br>PROGRAM</h1>

  <div class="badge badge--mission"><div class="badge-fill"></div><div class="badge-frame"></div><div class="badge-label">MISSION</div></div>
  <div class="badge badge--vision"><div class="badge-fill"></div><div class="badge-frame"></div><div class="badge-label">VISION</div></div>
  <div class="badge badge--values"><div class="badge-fill"></div><div class="badge-frame"></div><div class="badge-label">VALUES</div></div>

  <p class="statement statement--mission centered">To empower undergraduate students to pursue<br>excellence through scientific discovery,<br>clinical practice, and health promotion.</p>
  <p class="statement statement--vision centered">WSUH Kinesiology graduates are leaders<br>who excel in careers that enhance the quality<br>of life of individuals and communities.</p>
  <p class="statement statement--values centered">Student Success, Science, and Service</p>

  <h2 class="competency-heading centered" style="font-weight:400">Our Graduates Will Be Competent In :</h2>

  <div class="domain domain--science">THE SCIENCE OF KINESIOLOGY</div>
  <ul class="skills skills--science centered">
    <li>Foundational Concepts of Kinesiology</li>
    <li>Clinical Application</li>
    <li>Scientific Communication</li>
  </ul>

  <div class="domain domain--thinking">THINKING AND REASONING</div>
  <ul class="skills skills--thinking centered">
    <li>Critical Thinking</li>
    <li>Quantitative Reasoning</li>
    <li>Scientific Inquiry</li>
    <li>Concept Integration</li>
  </ul>

  <div class="domain domain--relationships">RELATIONSHIPS AND COMMUNICATION</div>
  <ul class="skills skills--relationships centered">
    <li>Cultural Competence</li>
    <li>Professionalism</li>
    <li>Leadership and Teamwork</li>
    <li>Service Orientation/Citizenship</li>
  </ul>

  <div class="domain domain--intrapersonal">INTRAPERSONAL GROWTH</div>
  <ul class="skills skills--intrapersonal centered">
    <li>Cultural Humility/Sensitivity</li>
    <li>Integrity</li>
    <li>Self-Directed</li>
    <li>Dependability</li>
    <li>Mission Oriented</li>
  </ul>
</body>
</html>
```